VOR Exterior Coatings

double sided. the front i want the name of the business each word on a new line with the VOR being bigger. id like teal, black and white colors. the back i want my contact info. Flat, no gloss. Something professional and I want to feel the letters bump put of the card. if possible maybe a paint sprayer in corner. not a car paint spray. (no tank on top of gun)
no vehicle paint sprayers. that means no tank on top of the gun. doesn't have to have a sprayer. black/dark background on the front. white back ground on back with info

```html
<!DOCTYPE html>
<html lang="en">
<head>
<meta charset="utf-8">
<title>VOR Exterior Coatings – Business Cards</title>
<link href="https://fonts.googleapis.com/css2?family=Bebas+Neue&family=Lato:wght@400;900&display=swap" rel="stylesheet">
<style>
  :root {
    --teal: #06827f;
    --teal-band: #077a77;
    --charcoal: #27282a;
    --ink: #141414;
    --paper: #f7f7f7;
    --white: #ffffff;
    --backdrop: #e6e3df;
    --back-top: #343434;
    --back-bottom: #272727;
    --emboss: #474747;
  }
  * { margin: 0; padding: 0; box-sizing: border-box; }
  html, body {
    width: 1200px; height: 1200px; overflow: hidden;
    background: var(--backdrop);
  }
  .canvas { position: relative; width: 1200px; height: 1200px; }

  .card {
    position: absolute; left: 262px; width: 686px; height: 392px;
    overflow: hidden;
  }

  /* Front card */
  .card--front { top: 165px; background: var(--paper); }
  .brand {
    position: absolute; left: 0; right: 0; top: 0; height: 248px;
    display: flex; flex-direction: column; align-items: center; justify-content: center;
    font-family: "Lato", sans-serif; font-weight: 900; color: var(--teal);
    padding-top: 6px;
  }
  .brand__mark { font-size: 124px; line-height: 0.9; letter-spacing: -2px; }
  .brand__line { font-size: 23px; line-height: 1; letter-spacing: 0.5px; margin-top: 8px; }

  .info-band {
    position: absolute; left: 0; right: 0; bottom: 0; height: 144px;
    display: flex; gap: 3px; background: var(--white);
  }
  .person {
    width: 341px; background: var(--teal-band); color: var(--white);
    padding: 24px 0 0 39px; font-family: "Lato", sans-serif;
  }
  .person__name { font-family: "Bebas Neue", sans-serif; font-size: 32px; line-height: 1; letter-spacing: 0.3px; }
  .person__role { font-size: 16px; line-height: 1.2; margin-top: 1px; }
  .person__address { font-size: 16px; line-height: 20px; margin-top: 7px; }

  .contact {
    flex: 1; background: var(--charcoal); color: var(--white);
    font-family: "Lato", sans-serif; font-size: 16px;
    list-style: none; padding: 28px 36px 0 0;
    display: flex; flex-direction: column; align-items: flex-end;
  }
  .contact__item { display: flex; align-items: center; gap: 7px; height: 20px; }
  .contact__icon { width: 14px; height: 14px; fill: var(--white); }

  /* Back card */
  .card--back {
    top: 653px;
    background: linear-gradient(180deg, var(--back-top), var(--back-bottom));
  }
  .brand--embossed { height: 100%; color: var(--emboss); padding-top: 0; }
  .brand--embossed .brand__mark { font-size: 150px; letter-spacing: -3px; }
  .brand--embossed .brand__line { font-size: 28px; margin-top: 6px; }
</style>
</head>
<body>
<main class="canvas">

  <section class="card card--front" aria-label="Front of business card">
    <div class="brand">
      <span class="brand__mark">VOR</span>
      <span class="brand__line">EXTERIOR COATINGS</span>
    </div>

    <div class="info-band">
      <div class="person">
        <p class="person__name">DANIEL BROOKS</p>
        <p class="person__role">Founder &amp; CEO</p>
        <p class="person__address">1420 Cedar Ridge Road<br>Anchorage, Alaska 34510</p>
      </div>

      <ul class="contact">
        <li class="contact__item">555-014-2290
          <svg class="contact__icon" viewBox="0 0 24 24" aria-hidden="true"><path d="M6.6 10.8a15.1 15.1 0 0 0 6.6 6.6l2.2-2.2c.3-.3.7-.4 1-.2 1.1.4 2.3.6 3.6.6.6 0 1 .4 1 1V20c0 .6-.4 1-1 1A17 17 0 0 1 3 4c0-.6.4-1 1-1h3.5c.6 0 1 .4 1 1 0 1.2.2 2.4.6 3.6.1.3 0 .7-.2 1l-2.3 2.2z"/></svg>
        </li>
        <li class="contact__item">555-018-7731
          <svg class="contact__icon" viewBox="0 0 24 24" aria-hidden="true"><path d="M7 1h10a2 2 0 0 1 2 2v18a2 2 0 0 1-2 2H7a2 2 0 0 1-2-2V3a2 2 0 0 1 2-2zm0 3v15h10V4H7zm5 16.2a1 1 0 1 0 0 2 1 1 0 0 0 0-2z"/></svg>
        </li>
        <li class="contact__item">info@vorexteriorcoatings.com
          <svg class="contact__icon" viewBox="0 0 24 24" aria-hidden="true"><path d="M2 6h20v12H2V6zm2 1.5 8 6 8-6v-.1H4v.1zm0 2V16h16V9.5l-8 6-8-6z"/></svg>
        </li>
        <li class="contact__item">www.vorexteriorcoatings.com
          <svg class="contact__icon" viewBox="0 0 24 24" aria-hidden="true"><path d="M12 2a10 10 0 1 0 0 20 10 10 0 0 0 0-20zm-1 17.9A8 8 0 0 1 4.2 10.5L9 15.3v1a2 2 0 0 0 2 2v1.6zm6.9-2.5a2 2 0 0 0-1.9-1.4h-1v-3a1 1 0 0 0-1-1H8v-2h2a1 1 0 0 0 1-1V7h2a2 2 0 0 0 2-2v-.4a8 8 0 0 1 2.9 12.8z"/></svg>
        </li>
      </ul>
    </div>
  </section>

  <section class="card card--back" aria-label="Back of business card">
    <div class="brand brand--embossed">
      <span class="brand__mark">VOR</span>
      <span class="brand__line">EXTERIOR COATINGS</span>
    </div>
  </section>

</main>
</body>
</html>
```